Roofing Contractor business card redesign

I want to redesign my business card with a fresh, eye catching concept

Target Market(s)

Residential Roofing Clients, potential employees, and subcontractors.

Industry/Entity Type

Business

Colors

Designer to choose colors to be used in the design.

Requirements
Nice to have
• I just want something that's more pleasing to the eye. You can use a combination of either / or of my logos.

```html
<!DOCTYPE html>
<html lang="en">
<head>
<meta charset="utf-8">
<title>Fair Hands Builders – Business Card</title>
<link href="https://fonts.googleapis.com/css2?family=Open+Sans:wght@400;600;800&display=swap" rel="stylesheet">
<style>
  :root{
    --bg:#e9e4dc;
    --paper:#f4f4f3;
    --ink-dark:#1c1c1d;
    --maroon:#5a1c1c;
    --band:#3a1e1e;
    --orange:#ef7b22;
    --gold:#f0b324;
    --grey:#555;
    --rule:#b9b9b9;
  }
  *{margin:0;padding:0;box-sizing:border-box}
  html,body{width:1200px;height:911px;overflow:hidden;background:var(--bg);font-family:"Open Sans",sans-serif}
  .stage{position:relative;width:1200px;height:911px}
  .card{position:absolute;top:95px;width:420px;height:720px;border-radius:26px;overflow:hidden;box-shadow:0 10px 30px rgba(0,0,0,.18)}
  .card--front{left:150px;background:var(--paper)}
  .card--back{left:630px;background:var(--ink-dark)}

  .brand{position:absolute;left:0;right:0;top:70px;display:flex;justify-content:center;align-items:center;gap:14px}
  .brand__mark{width:38px;height:38px;border-radius:50%;background:var(--orange);flex:none}
  .brand__name{font-weight:800;color:var(--maroon);font-size:40px;line-height:1;letter-spacing:-1px;text-align:left}
  .brand__name small{display:block;font-size:19px;letter-spacing:0;margin-top:6px}

  .contact{position:absolute;left:46px;top:420px;display:flex}
  .contact__icons{width:30px;display:flex;flex-direction:column;align-items:center;gap:0}
  .contact__icons svg{fill:var(--maroon)}
  .contact__rule{width:1px;background:var(--rule);margin:0 18px 0 12px}
  .contact__text{font-size:14.5px;color:var(--grey);line-height:1.45}
  .contact__name{font-weight:600;font-size:19px;color:var(--ink-dark);letter-spacing:.3px}
  .contact__role{color:var(--orange);font-size:16px;line-height:1.3}
  .contact__details{margin-top:12px}

  .back-brand{position:absolute;top:92px;left:0;right:0;text-align:center;color:#fff;font-weight:800;font-size:50px;line-height:1;letter-spacing:-1px}
  .back-brand small{display:block;font-size:20px;letter-spacing:0;margin-top:6px}
  .crew-art{position:absolute;left:60px;right:30px;top:410px;height:225px;border-radius:110px 110px 8px 8px;
    background:linear-gradient(160deg,var(--gold) 0%,var(--orange) 55%,#7a3a16 100%)}
  .back-band{position:absolute;left:0;right:0;bottom:0;height:48px;background:var(--band);color:#eee;
    font-size:14px;letter-spacing:5px;display:flex;align-items:center;justify-content:center}
</style>
</head>
<body>
<main class="stage">
  <section class="card card--front">
    <div class="brand">
      <div class="brand__name">Fair Hands<small>Builders, Inc.</small></div>
      <span class="brand__mark"></span>
    </div>

    <div class="contact">
      <div class="contact__icons">
        <svg width="16" height="18" viewBox="0 0 16 18" style="margin-top:4px"><circle cx="8" cy="5" r="4"/><path d="M0 18c0-5 3.5-7 8-7s8 2 8 7z"/></svg>
        <svg width="14" height="18" viewBox="0 0 14 18" style="margin-top:48px"><path d="M7 0a7 7 0 0 0-7 7c0 5 7 11 7 11s7-6 7-11a7 7 0 0 0-7-7zm0 10a3 3 0 1 1 0-6 3 3 0 0 1 0 6z"/></svg>
        <svg width="14" height="14" viewBox="0 0 14 14" style="margin-top:22px"><path d="M3 0l3 3-2 2a8 8 0 0 0 5 5l2-2 3 3-2 3C6 14 0 8 0 2z"/></svg>
        <svg width="14" height="12" viewBox="0 0 14 12" style="margin-top:8px"><path d="M0 0h14v12H0zM1.5 1.5 7 6l5.5-4.5" fill="none" stroke="#5a1c1c" stroke-width="1.6"/></svg>
        <svg width="14" height="14" viewBox="0 0 14 14" style="margin-top:8px"><circle cx="7" cy="7" r="6" fill="none" stroke="#5a1c1c" stroke-width="1.6"/><path d="M1 7h12M7 1c-3 3-3 9 0 12M7 1c3 3 3 9 0 12" fill="none" stroke="#5a1c1c" stroke-width="1.2"/></svg>
      </div>
      <div class="contact__rule"></div>
      <div class="contact__text">
        <div class="contact__name">SAM ROWLEY</div>
        <div class="contact__role">Keel Certified Roof Inspector<br>Licensed Property Adjuster</div>
        <div class="contact__details">
          4410 Elm Ridge Road Suite 118<br>
          Austin, TX 78701<br>
          (555) 210-4800<br>
          (555) 318-2290<br>
          sam@fairhandstx.com<br>
          www.fairhandstx.com
        </div>
      </div>
    </div>
  </section>

  <section class="card card--back">
    <div class="back-brand">Fair Hands<small>Builders, Inc.</small></div>
    <div class="crew-art" role="img" aria-label="Illustration of three builders holding hammers, arms crossed"></div>
    <div class="back-band">WWW.FAIRHANDSTX.COM</div>
  </section>
</main>
</body>
</html>
```